House-share and Room Rental Website (With Focus on the Bedroom Landing Page)

Looking for website design for our House-share (executive accommodation) and room rental business.

Our company name is: Lodgivo could also be written as LodGivo or lodgivo. Either is fine .. just looking for a nice clean catchy logo to go with the design.

EXAMPLES
These are examples of other websites in this field that are doing well. this is a kind of baseline.
https://nestpartners-example.com.au/
https://www.bunkora-example.com/
https://www.dwelzy-example.com/
https://www.habiquo-example.net/
https://www.cohabiscout-example.com.au/

Our business model is to rent rooms to people looking for high-quality accommodation. We fill the gap between those looking to rent rooms and those with rooms to rent. However, our model is slightly different from those already on the market as we looking to fill a massive gap in the market delivering upmarket rooms for rent.(Executive Accommodation) also in the back end will be coupled with a self management process in the back end.

We offer executive style accommodation that stands out above the rest. With special extras like fire safety.. and management processes that create happier homes. We are looking for a web design package that can help us grow and scale our business. We need a design that is captivating

Our MAIN focus is having a room landing page that stands out from the rest... The core of our business will rely on the promotion of the rooms in a share house... so the whole design relies on the BEDROOM landing page to drive results.

Target Market(s)

We have 2 markets we are aiming at ... the first market is people offering rooms to rent who want the highest rental return. The second market is people looking to rent safe, high-quality rooms, in houses that are well managed and looked after.

Industry/Entity Type

Share Economy

Logo Text

LodGivo

Number of Pages Required

5+ page

Font styles to use
Sans Serif

Colors
3276b5

Requirements
Must have
• A messaging system whereby we can create direct communication between those offering rooms and those looking for rooms.
• A call to action that says " Schedule an Inspection"
• Landing page for promoting rooms
• A home page for showing stock.
• Profile page for those selling rooms
• Profile page for those looking for rooms.
• A scheduling calendar for booking inspections
Nice to have
• Pages where new residents can lock in a room.. pay bond and rents.. and sign contracts
• Notifications
• SMS capabilities in the backend.
Should not have
• No script or handwriting fonts.

```html
<!DOCTYPE html>
<html lang="en">
<head>
<meta charset="utf-8">
<title>LodGivo – Classic bed room</title>
<link href="https://fonts.googleapis.com/css2?family=Dosis:wght@300;400;500;600;700&display=swap" rel="stylesheet">
<style>
  :root {
    --brand: #3276b5;
    --brand-soft: #7fa5cf;
    --dark: #343434;
    --heading: #4a4a4a;
    --ink: #3a3a3a;
    --body: #555555;
    --muted: #9a9a9a;
    --faint: #ababab;
    --line: #e2e2e2;
    --band: #efefef;
    --card: #eeeeee;
    --white: #ffffff;
  }
  * { box-sizing: border-box; margin: 0; padding: 0; }
  html, body { width: 1200px; height: 1000px; overflow: hidden; background: var(--white); }
  body { font-family: "Dosis", sans-serif; color: var(--ink); position: relative; -webkit-font-smoothing: antialiased; -moz-osx-font-smoothing: grayscale; }
  .page { position: absolute; left: 414px; top: 34px; width: 373px; height: 931px; background: var(--white); box-shadow: 0 10px 40px rgba(0,0,0,0.12); overflow: hidden; }
  .abs { position: absolute; }

  /* header */
  .site-header { left: 0; top: 0; width: 373px; height: 28px; background: var(--dark); }
  .back-link { left: 13px; top: 9px; }
  .brand-name { left: 0; width: 373px; top: 7px; text-align: center; color: var(--brand); font-size: 11px; font-weight: 600; letter-spacing: 0.2px; }

  /* hero gallery */
  .hero-photo { top: 28px; height: 121px; }
  .photo-kitchen { left: 0; width: 102px; background: linear-gradient(180deg, #e9e6e3 0%, #d8d2cc 35%, #b9aea5 55%, #d6d2ce 75%, #e4e2e0 100%); opacity: .8; }
  .photo-bedroom { left: 102px; width: 166px; background: linear-gradient(180deg, #f1f1ef 0%, #e4e5e3 25%, #b9c3c2 45%, #d9dcda 58%, #cfd0d0 70%, #8f8d8a 84%, #a9a7a4 100%); }
  .photo-bathroom { left: 268px; width: 105px; background: linear-gradient(180deg, #f7f7f7 0%, #ececec 45%, #f9f9f9 70%, #e8e8e8 100%); opacity: .85; }
  .gallery-arrow { top: 81px; width: 14px; height: 14px; border: 1px solid #555; border-radius: 50%; }
  .gallery-count { left: 240px; top: 135px; width: 51px; height: 14px; background: rgba(40,40,40,.85); color: #ddd; font-size: 4.5px; line-height: 14px; text-align: center; }

  /* listing */
  .listing-title { left: 34px; top: 166px; font-size: 13px; font-weight: 300; color: var(--heading); }
  .listing-address { left: 34px; top: 183px; font-size: 4.5px; color: var(--body); }
  .map-link { left: 34px; top: 191px; font-size: 4.5px; color: var(--brand); display: flex; align-items: center; gap: 2px; }
  .price { right: 145px; top: 172px; font-size: 8px; font-weight: 600; color: var(--brand); }
  .price-note { right: 145px; top: 184px; font-size: 4px; color: var(--muted); text-align: right; line-height: 8px; }
  .price-note b { color: var(--body); font-weight: 400; }
  .rule { left: 34px; width: 195px; height: 1px; background: var(--line); }

  .features { left: 34px; top: 225px; width: 195px; display: grid; grid-template-columns: repeat(4, 1fr); row-gap: 15px; }
  .feature { text-align: center; font-size: 4px; color: #666; }
  .feature svg { display: block; margin: 0 auto 5px; }
  .feature b { font-weight: 600; color: #333; }

  .description { left: 34px; top: 311px; width: 195px; font-size: 4.4px; line-height: 6.7px; color: var(--body); }
  .description strong { color: #222; }
  .description-note { left: 34px; top: 353px; width: 195px; font-size: 4.2px; line-height: 6.7px; color: var(--faint); }
  .cta-inspection { left: 34px; top: 379px; width: 68px; height: 14px; border: 1px solid var(--brand); color: var(--brand); font-size: 4.3px; font-weight: 600; text-align: center; line-height: 12px; letter-spacing: .2px; }

  /* host card */
  .host-card { left: 242px; top: 171px; width: 96px; height: 129px; background: var(--card); }
  .host-name { right: 46px; top: 16px; text-align: right; font-size: 5.5px; font-weight: 600; color: #333; line-height: 7px; }
  .host-name span { display: block; font-size: 3.6px; font-weight: 400; color: var(--brand); }
  .host-avatar { left: 52px; top: 11px; width: 32px; height: 32px; background: linear-gradient(135deg, #8fc2d6, #b9c9cf 55%, #cdb4a3); }
  .host-phone { left: 12px; top: 34px; font-size: 3.8px; color: #444; }
  .host-phone i { font-style: normal; color: var(--muted); }
  .message-box { left: 14px; top: 57px; width: 68px; height: 40px; background: var(--white); font-size: 3.8px; color: var(--muted); padding: 4px; }
  .send-button { left: 14px; top: 100px; width: 68px; height: 14px; background: var(--brand); color: var(--white); font-size: 4.3px; font-weight: 600; line-height: 14px; text-align: center; }

  /* amenities */
  .band-grey { left: 0; top: 417px; width: 373px; height: 185px; background: var(--band); }
  .section-title { font-size: 13px; font-weight: 300; color: var(--heading); }
  .section-sub { font-size: 4px; color: var(--faint); }
  .amenity-list { list-style: none; font-size: 4.3px; color: var(--body); }
  .amenity-list li { height: 10.2px; position: relative; padding-left: 7px; }
  .amenity-list li::before { content: ""; position: absolute; left: 0; top: 2px; width: 2px; height: 2px; border-radius: 50%; background: #bbb; }
  .amenity-photo { left: 187px; top: 453px; width: 151px; height: 116px; background: linear-gradient(90deg, rgba(255,255,255,0) 0%, rgba(255,255,255,0) 38%, rgba(120,150,70,.55) 52%, rgba(255,255,255,0) 66%), linear-gradient(180deg, #d8cfc3 0%, #f3f1ee 22%, #f7f6f4 60%, #e6e1da 100%); box-shadow: 0 3px 8px rgba(0,0,0,.18); }

  .public-text { left: 34px; top: 656px; width: 132px; font-size: 4px; line-height: 6.2px; color: var(--body); }
  .public-note { left: 34px; top: 694px; width: 132px; font-size: 4px; line-height: 6.2px; color: var(--faint); }
  .area-map { left: 187px; top: 638px; width: 153px; height: 117px; background: linear-gradient(160deg, #ececec, #e2e2e2 50%, #ebebeb); box-shadow: 0 3px 8px rgba(0,0,0,.15); }
  .map-pin-area { left: 54px; top: 36px; width: 44px; height: 44px; border-radius: 50%; background: rgba(50,118,181,.5); color: var(--white); font-size: 5.5px; text-align: center; line-height: 44px; }
  .map-zoom { left: 2px; top: 88px; width: 9px; height: 18px; background: var(--white); font-size: 7px; line-height: 9px; text-align: center; color: #444; }

  /* footer */
  .site-footer { left: 0; top: 793px; width: 373px; height: 138px; background: var(--dark); color: #bbb; }
  .footer-title { left: 34px; top: 31px; color: var(--white); font-size: 9px; font-weight: 500; }
  .footer-text { left: 34px; top: 48px; width: 130px; font-size: 3.8px; line-height: 6.2px; color: #aaa; }
  .footer-email { left: 34px; top: 97px; font-size: 4px; color: var(--brand-soft); }
  .connect-title { right: 34px; top: 34px; color: var(--white); font-size: 5px; font-weight: 600; }
  .social-row { left: 280px; top: 51px; display: flex; gap: 4px; }
  .social-dot { width: 11px; height: 11px; border-radius: 50%; background: var(--brand); }
  .payment-row { right: 34px; top: 99px; display: flex; gap: 4px; align-items: center; }
  .payment-chip { width: 8px; height: 4px; background: #5a5a5a; border-radius: 1px; }
</style>
</head>
<body>
<main class="page">

  <header class="site-header abs">
    <svg class="back-link abs" width="11" height="9" viewBox="0 0 11 9" aria-label="Back"><path d="M10 4.5H1M4.5 1 1 4.5 4.5 8" fill="none" stroke="#777" stroke-width="0.8"/></svg>
    <div class="brand-name abs">LodGivo</div>
  </header>

  <section class="gallery">
    <div class="hero-photo photo-kitchen abs" role="img" aria-label="Photo of the shared kitchen"></div>
    <div class="hero-photo photo-bedroom abs" role="img" aria-label="Photo of the bright bedroom with double bed and large window"></div>
    <div class="hero-photo photo-bathroom abs" role="img" aria-label="Photo of the white bathroom"></div>
    <svg class="gallery-arrow abs" style="left:75px" viewBox="0 0 14 14" aria-label="Previous photo"><path d="M8 4 5 7l3 3" fill="none" stroke="#444" stroke-width="0.8"/></svg>
    <svg class="gallery-arrow abs" style="left:284px" viewBox="0 0 14 14" aria-label="Next photo"><path d="M6 4l3 3-3 3" fill="none" stroke="#444" stroke-width="0.8"/></svg>
    <div class="gallery-count abs"><b style="color:#fff">3</b>/10 &nbsp;View Gallery</div>
  </section>

  <section class="listing">
    <h1 class="listing-title abs">Classic bed room</h1>
    <p class="listing-address abs">42 Harbour Lane, Sydney</p>
    <p class="map-link abs"><svg width="4" height="5" viewBox="0 0 4 5"><path d="M2 5C.5 3 0 2.3 0 1.8A2 2 0 0 1 4 1.8C4 2.3 3.5 3 2 5Z" fill="#3276b5"/></svg>Location map</p>
    <p class="price abs">350 AUD</p>
    <p class="price-note abs">( Minimum 3 months contract )<br><b>Utilities excluded</b></p>
    <div class="rule abs" style="top:208px"></div>

    <div class="features abs">
      <div class="feature"><svg width="13" height="13" viewBox="0 0 12 12" fill="none" stroke="#3276b5" stroke-width=".6"><circle cx="4" cy="2" r="1.2"/><circle cx="8" cy="2" r="1.2"/><path d="M3 4h2v4H4.5v3h-1V8H3zM7 4h2l.8 4H8.5v3h-1V8H6.2z"/></svg>Gender - <b>Male</b></div>
      <div class="feature"><svg width="13" height="13" viewBox="0 0 12 12" fill="none" stroke="#3276b5" stroke-width=".6"><path d="M1 6 6 1.5 11 6M2.5 5v6h7V5"/><circle cx="6" cy="7" r="1"/></svg>Room type - <b>Private</b></div>
      <div class="feature"><svg width="13" height="13" viewBox="0 0 12 12" fill="none" stroke="#3276b5" stroke-width=".6"><rect x="1" y="1" width="10" height="10"/><path d="M3 3l2 2M9 3 7 5M3 9l2-2M9 9 7 7"/></svg>Size of room - <b>20</b> sqm</div>
      <div class="feature"><svg width="13" height="13" viewBox="0 0 12 12" fill="none" stroke="#3276b5" stroke-width=".6"><rect x="1.5" y="1" width="9" height="10"/><path d="M4.5 9V3.5h2a1.5 1.5 0 0 1 0 3h-2"/></svg>Parking - <b>Private</b></div>
      <div class="feature"><svg width="13" height="13" viewBox="0 0 12 12" fill="none" stroke="#3276b5" stroke-width=".6"><path d="M1 9h10M1.5 9V6h9v3M2.5 6V4h7v2M1.5 9v1.5M10.5 9v1.5"/></svg>Bed size - <b>Double</b></div>
      <div class="feature"><svg width="13" height="13" viewBox="0 0 12 12" fill="none" stroke="#3276b5" stroke-width=".6"><rect x="1" y="1.5" width="10" height="9"/><path d="M1 3.5h10M3 6h6M3 8h4"/></svg>internet speed - <b>High</b></div>
      <div class="feature"><svg width="13" height="13" viewBox="0 0 12 12" fill="none" stroke="#3276b5" stroke-width=".6"><path d="M1 6h10v1.5a2.5 2.5 0 0 1-2.5 2.5h-5A2.5 2.5 0 0 1 1 7.5zM2.5 6V2.5a1 1 0 0 1 2 0M3 10l-.5 1M9 10l.5 1"/></svg>Bathroom - <b>Private</b></div>
      <div class="feature"><svg width="13" height="13" viewBox="0 0 12 12" fill="none" stroke="#3276b5" stroke-width=".6"><rect x="1" y="7" width="8" height="1.8"/><path d="M10 7v1.8M10 6c0-1.5-1.5-1.5-1.5-3M2 2l8 8"/></svg>Smoking - <b>Non</b></div>
    </div>
    <div class="rule abs" style="top:300px"></div>

    <p class="description abs"><strong>Aenean convallis sit amet</strong> enim lacinia maximus. Lorem ipsum dolor sit amet, consectetur adipiscing elit. Cras dignissim, lorem sit amet consequat tempor, erat mi dapibus nibh, quis vehicula nisi lectus ac leo. Maecenas ultrices a ex id tincidunt. Nullam justo ipsum, lobortis quis mauris id, dignissim ullamcorper nisl. Nunc nec felis a turpis congue molestie ac id orci. Donec venenatis est eget ultrices gravida. Praesent porttitor commodo hendrerit. Mauris laoreet urna in quam lacinia tincidunt.</p>
    <p class="description-note abs">Pellentesque habitant morbi tristique senectus et netus et malesuada fames ac turpis egestas. Duis ultrices egestas erat eget rhoncus.</p>
    <div class="cta-inspection abs">SCHEDULE AN INSPECTION</div>

    <aside class="host-card abs">
      <p class="host-name abs">Liam Carter<span>Online</span></p>
      <div class="host-avatar abs" role="img" aria-label="Profile photo of the host"></div>
      <p class="host-phone abs">0400 123 456 &nbsp;<i>Mobile</i></p>
      <div class="message-box abs">Write message</div>
      <div class="send-button abs">SEND</div>
    </aside>
  </section>

  <section class="band-grey abs">
    <h2 class="section-title abs" style="left:34px;top:32px">Room amenities</h2>
    <p class="section-sub abs" style="left:34px;top:49px">Lorem ipsum dolor sit amet</p>
    <ul class="amenity-list abs" style="left:34px;top:67px">
      <li>Fully furnished</li><li>TV</li><li>Storage space</li><li>Study Desk</li><li>Wardrobe</li><li>Ensuite shower</li><li>Kitchenette</li>
    </ul>
  </section>
  <div class="amenity-photo abs" role="img" aria-label="Photo of a bright living space with a potted bamboo plant"></div>

  <section class="public">
    <h2 class="section-title abs" style="left:34px;top:634px">Public amenities</h2>
    <p class="public-text abs">Transport options available lorem ipsum, lobortis quis mauris id, dignissim ullamcorper nisl. Nunc nec felis a turpis congue molestie ac id orci. Donec venenatis est eget ultrices gravida. Praesent porttitor commodo hendrerit. Mauris laoreet urna in quam lacinia tincidunt.</p>
    <p class="public-note abs">Pellentesque habitant morbi tristique senectus et netus et malesuada fames ac turpis egestas. Duis ultrices egestas erat eget rhoncus.</p>
    <ul class="amenity-list abs" style="left:34px;top:715px">
      <li>Trains</li><li>Busses</li><li>1 Km to the Sydney harbour bridge</li><li>Shortest route to the city</li>
    </ul>
    <div class="area-map abs" role="img" aria-label="Street map of the surrounding neighbourhood">
      <div class="map-pin-area abs">WE ARE HERE</div>
      <div class="map-zoom abs">+<br>&minus;</div>
    </div>
  </section>

  <footer class="site-footer abs">
    <h3 class="footer-title abs">About the LodGivo</h3>
    <p class="footer-text abs">Lorem ipsum dolor sit amet, consectetur adipiscing elit. Duis sit amet metus laoreet, sollicitudin quam vitae, lacus nisl. Etiam laoreet at ipsum vel vestibulum. Suspendisse efficitur eros id pharetra malesuada. Morbi non ipsum nec lectus pretium viverra sit amet diam. Integer id nisi justo. Fusce dignissim, pellentesque eget pharetra vitae, tincidunt id neque. Aliquam nisl metus, consequat in malesuada nec, ullamcorper a eros.</p>
    <p class="footer-email abs">hello@lodgivo.com.au</p>
    <p class="connect-title abs">Connect with us</p>
    <div class="social-row abs"><span class="social-dot"></span><span class="social-dot"></span><span class="social-dot"></span><span class="social-dot"></span></div>
    <div class="payment-row abs"><span class="payment-chip"></span><span class="payment-chip"></span><span class="payment-chip"></span><span class="payment-chip"></span></div>
  </footer>

</main>
</body>
</html>
```